Email Marketing Campaign Brief

We want to do an email marketing campaign around our consulting services. The attached documents provide back ground on our work but additional copy can be found below:

KV7lr is committed to helping you, the educator, make informed buying decisions based on local control and independent reviews through a simple, impartial and an effective approach.
In education, there exists a vast array of educational solutions – such as reading, science, language arts, and math curricula; school-wide reform programs; interventions; after-school programs; and new educational technologies. In the marketplace, providers could, and most do, claim to be able to improve educational outcomes and, in many cases, they all pretend to be supported by evidence. But a cursory review reveals that most evidence consists of poorly designed or advocacy-driven studies with some providers having such inadequate research as could only be described as case studies.

So the problem for State and local education officials is that they must sort through a myriad of such claims to decide which solutions merit consideration for their schools and classrooms. One US official stated the problem saying “many of these practitioners have seen interventions (solutions), introduced with great fanfare as being able to produce dramatic gains, come and go over the years, yielding little in the way of positive and lasting change – a perception confirmed by the flat achievement results over the past 30 years in the Federal Survey of Scholastic Attainment long-term trend”

KV7lr is a process by which we make you, the educator, the locus of control

OUR Approach:
With four simple, yet highly effective steps, KV7lr guides educators through an informed buying process that’s based on local control and review.

Step 1 — Research, Review, and Evaluation Criteria

Step 2 — Cost / Benefit Analysis

Step 3 — Education Survey & Culture Scan

Step 4 — Negotiation & Representation

Target Market(s)

Education

Industry/Entity Type

Marketing

Font styles to use
Sans Serif

Colors
f9b46a
f37122

Requirements
Must have
• HTML format that can be used in an Email Campaign
Nice to have
• Additional Copy in Word

```html
<!DOCTYPE html>
<html lang="en">
<head>
<meta charset="utf-8">
<title>KV7lr Email Campaign</title>
<link rel="stylesheet" href="https://fonts.googleapis.com/css2?family=Open+Sans:ital,wght@0,400;0,600;0,700;0,800;1,700;1,800&display=swap">
<style>
  :root {
    --orange: #f37122;
    --orange-light: #f9b46a;
    --green: #8dc63f;
    --green-light: #b5dc6e;
    --blue: #1e88d9;
    --ink: #2b2b2b;
    --muted: #555;
    --page: #e4e5e8;
    --white: #ffffff;
  }
  * { box-sizing: border-box; margin: 0; padding: 0; }
  html, body { width: 1200px; height: 810px; overflow: hidden; }
  body {
    background: var(--page);
    font-family: "Open Sans", Arial, sans-serif;
    color: var(--ink);
    display: flex;
    justify-content: center;
  }
  .email {
    width: 700px;
    height: 810px;
    background: var(--white);
    display: flex;
    flex-direction: column;
    box-shadow: 0 0 18px rgba(0,0,0,.12);
  }

  /* Hero */
  .hero {
    position: relative;
    height: 222px;
    flex: none;
  }
  .hero-photo {
    position: absolute; inset: 0;
    background: linear-gradient(100deg, #cfe6f5 0%, #f3d9c4 38%, #e9eef2 70%, #ffffff 100%);
  }
  .brand-box {
    position: absolute;
    right: 36px; top: 96px;
    width: 210px; height: 74px;
    background: var(--orange);
    color: var(--white);
    display: flex; flex-direction: column; justify-content: center;
    padding-left: 22px;
  }
  .brand-name { font-size: 30px; font-weight: 400; letter-spacing: .5px; line-height: 1; }
  .brand-tagline { font-size: 9.5px; font-weight: 600; margin-top: 6px; }

  /* Headline */
  .headline { padding: 10px 30px 4px; flex: none; }
  .headline h1 {
    color: var(--blue);
    font-size: 25px; font-weight: 800; font-style: italic;
    line-height: 1.1;
  }
  .headline h2 {
    color: var(--orange);
    font-size: 15px; font-weight: 700; font-style: italic;
    margin-top: 2px;
  }

  /* Body copy */
  .intro {
    display: grid;
    grid-template-columns: 1fr 1fr;
    gap: 22px;
    padding: 6px 30px 10px;
    font-size: 8.2px;
    line-height: 1.38;
    color: var(--muted);
    flex: none;
  }
  .intro p + p { margin-top: 4px; }
  .intro .name { color: var(--orange); font-weight: 700; }
  .intro h3 { font-size: 10.5px; color: var(--ink); font-weight: 800; margin-top: 5px; }

  /* Program section */
  .program {
    position: relative;
    flex: 1;
    background: var(--green);
    padding: 30px 24px 12px;
  }
  .program-wave { position: absolute; top: -1px; left: 0; width: 100%; height: 28px; }
  .program-band {
    background: var(--orange);
    color: var(--white);
    text-align: center;
    padding: 7px 10px 8px;
    margin: 0 -24px 12px;
  }
  .program-band h3 { font-size: 15px; font-weight: 800; letter-spacing: .5px; }
  .program-band p { font-size: 10px; font-weight: 700; color: #3a1a05; }
  .steps {
    display: grid;
    grid-template-columns: 1fr 1fr;
    gap: 12px 18px;
  }
  .step { display: flex; gap: 10px; align-items: center; }
  .step-photo {
    position: relative;
    width: 128px; height: 76px; flex: none;
    border: 3px solid var(--orange);
    border-radius: 4px;
  }
  .step-photo.kids { background: linear-gradient(135deg, #f2c9a8, #e58a6a 60%, #6fa8d6); }
  .step-photo.chart { background: linear-gradient(135deg, #ffffff, #e9ecf3 55%, #c9d2e4); }
  .step-photo.survey { background: linear-gradient(135deg, #f5f5f5, #d6d6d6 55%, #9a8d84); }
  .step-photo.meeting { background: linear-gradient(135deg, #e4c6ad, #b98566 55%, #5f4a42); }
  .step-number {
    position: absolute; right: -10px; bottom: -10px;
    width: 26px; height: 26px; border-radius: 50%;
    background: var(--orange);
    border: 2px solid var(--white);
    color: var(--white);
    font-weight: 800; font-size: 13px;
    display: flex; align-items: center; justify-content: center;
  }
  .step h4 { font-size: 10.5px; font-weight: 800; color: #1c1c1c; line-height: 1.2; }
  .step ul { list-style: none; margin-top: 3px; }
  .step li { font-size: 8.5px; color: #1f3a0b; line-height: 1.35; }
  .step li::before { content: "• "; color: var(--orange); font-weight: 700; }

  /* Footer */
  .cta {
    flex: none;
    height: 66px;
    background: var(--orange);
    color: var(--white);
    display: flex; align-items: center; justify-content: space-between;
    padding: 0 30px;
  }
  .cta-text p { font-size: 12px; font-weight: 600; }
  .cta-text strong { font-size: 13.5px; font-weight: 800; display: block; }
  .cta-phone { font-size: 17px; font-weight: 800; }
  .social { display: flex; gap: 8px; }
  .social span {
    width: 24px; height: 24px; border-radius: 50%;
    background: var(--white);
  }
  .site {
    flex: none;
    height: 22px;
    background: var(--orange-light);
    color: #5a2a0a;
    font-size: 10px; font-weight: 700;
    text-align: center;
    line-height: 22px;
  }
</style>
</head>
<body>
<main class="email">

  <header class="hero">
    <div class="hero-photo" role="img" aria-label="Photo of smiling schoolchildren and a teacher gathered together"></div>
    <div class="brand-box">
      <span class="brand-name">KV7lr</span>
      <span class="brand-tagline">Research • Policy • Practice</span>
    </div>
  </header>

  <section class="headline">
    <h1>We help you to build geniuses</h1>
    <h2>Research, Teaching, Learning</h2>
  </section>

  <section class="intro">
    <div>
      <p><span class="name">KV7lr</span> is committed to helping you, the educator, make informed buying decisions based on local control and independent reviews through a simple, impartial and an effective approach.</p>
      <p>In education, there exists a vast array of educational solutions – such as reading, science, language arts, and math curricula; school-wide reform programs; interventions; after-school programs; and new educational technologies. In the marketplace, providers could, and most do, claim to be able to improve educational outcomes and, in many cases, they all pretend to be supported by evidence. But a cursory review reveals that most evidence consists of poorly designed or advocacy-driven studies.</p>
      <p>So the problem for State and local education officials is that they must sort through a myriad of such claims to decide which solutions merit consideration for their schools and classrooms.</p>
    </div>
    <div>
      <p>One US official stated the problem saying “many of these practitioners have seen interventions (solutions), introduced with great fanfare as being able to produce dramatic gains, come and go over the years, yielding little in the way of positive and lasting change – a perception confirmed by the flat achievement results over the past 30 years in the Federal Survey of Scholastic Attainment long-term trend”</p>
      <p><span class="name">KV7lr</span> is a process by which we make you, the educator, the locus of control.</p>
      <h3>OUR Approach:</h3>
      <p>With four simple, yet highly effective steps, KV7lr guides educators through an informed buying process that’s based on local control and review.</p>
    </div>
  </section>

  <section class="program">
    <svg class="program-wave" viewBox="0 0 700 28" preserveAspectRatio="none" aria-hidden="true">
      <path d="M0 0 H700 V10 C560 30 420 2 300 14 C180 26 80 6 0 16 Z" fill="#ffffff"/>
    </svg>
    <div class="program-band">
      <h3>PROGRAM IMPLEMENTATION</h3>
      <p>Independent Review Connected to School District Need and Stakeholder</p>
    </div>
    <div class="steps">
      <article class="step">
        <div class="step-photo kids" role="img" aria-label="Photo of students working at desks in a classroom"><span class="step-number">1</span></div>
        <div>
          <h4>Research, Review and Evaluation Criteria</h4>
          <ul><li>Program and vendor scan</li><li>Independent evidence review</li></ul>
        </div>
      </article>
      <article class="step">
        <div class="step-photo chart" role="img" aria-label="Photo of printed charts and graphs on a desk"><span class="step-number">2</span></div>
        <div>
          <h4>Cost / Benefit Analysis</h4>
          <ul><li>Cost per student outcome</li><li>Long-term value forecast</li></ul>
        </div>
      </article>
      <article class="step">
        <div class="step-photo survey" role="img" aria-label="Photo of a hand filling in a paper survey with a pen"><span class="step-number">3</span></div>
        <div>
          <h4>Education Survey and Culture Scan</h4>
          <ul><li>Stakeholder input survey</li><li>District culture readiness</li></ul>
        </div>
      </article>
      <article class="step">
        <div class="step-photo meeting" role="img" aria-label="Photo of two professionals in a consultation meeting"><span class="step-number">4</span></div>
        <div>
          <h4>Negotiation and Representation</h4>
          <ul><li>Contract terms and pricing</li><li>Advocacy on your behalf</li></ul>
        </div>
      </article>
    </div>
  </section>

  <footer>
    <div class="cta">
      <div class="cta-text">
        <p>KV7lr help you make informed buying decisions.</p>
        <strong>Contact us today for a no-cost consultation</strong>
      </div>
      <div class="cta-phone">(555) 014-2033</div>
      <div class="social" aria-label="Social channels"><span></span><span></span><span></span><span></span></div>
    </div>
    <div class="site">www.KV7lr.com</div>
  </footer>

</main>
</body>
</html>
```